Bork Ventures, Inc. Website redesign

Revamp the website, it is old and outdated. www.borkventuresinc.example

Target Market(s)

Information Technology Consulting and Staffing

Coding

Coded - Design and coding required

Number of Pages Required

5+ page

Colors

Designer to choose colors to be used in the design.

Requirements
Must have
• Outlined text boxes just like from the Tolvane.example site. A clean look

```html
<!DOCTYPE html>
<html lang="en">
<head>
<meta charset="utf-8">
<title>Bork Ventures, Inc. — IT Consulting</title>
<link rel="stylesheet" href="https://fonts.googleapis.com/css2?family=Exo+2:wght@400;500;600;700&family=Open+Sans:wght@400;600&display=swap">
<style>
:root{
  --red:#8b0c25;
  --red-dark:#6e0a1d;
  --red-light:#a3173a;
  --ink:#222;
  --body:#444;
  --muted:#f2c9d2;
  --nav-dark:#0b0b0b;
  --pink-bg:#fdf1f4;
  --footer:#242424;
  --white:#fff;
}
*{box-sizing:border-box;margin:0;padding:0}
html,body{width:1200px;height:3897px;overflow:hidden;background:var(--white)}
body{position:relative;font-family:Arial,Helvetica,sans-serif;color:var(--body)}
.abs{position:absolute}

/* header */
.site-header{left:0;top:0;width:1200px;height:115px}
.brand{left:110px;top:40px;display:flex;align-items:center;gap:10px;white-space:nowrap}
.brand-name{font-family:"Exo 2",sans-serif;font-weight:700;font-size:24px;color:var(--ink);letter-spacing:1px;white-space:nowrap}
.brand-mark{width:20px;height:20px;background:var(--red);flex:none}
.tagline{left:374px;top:42px;font-family:"Exo 2",sans-serif;font-size:24px;color:#555;font-variant:small-caps;white-space:nowrap}
.call{left:818px;top:30px;display:flex;align-items:center;gap:12px}
.call-icon{width:52px;height:52px;border-radius:50%;background:var(--red);display:flex;align-items:center;justify-content:center}
.call-text{font-family:"Exo 2",sans-serif;font-weight:700;font-size:19px;color:var(--ink);white-space:nowrap}

.main-nav{left:0;top:115px;width:1200px;height:62px;background:var(--red)}
.main-nav ul{list-style:none;position:absolute;left:110px;top:0;height:62px;display:flex;align-items:center}
.main-nav li{font-family:"Exo 2",sans-serif;font-size:13px;font-weight:500;color:var(--white);height:62px;display:flex;align-items:center;padding:0 38px;position:relative;white-space:nowrap}
.main-nav li+li::before{content:"|";position:absolute;left:-3px;opacity:.7}
.main-nav li.active{background:var(--nav-dark);width:162px;justify-content:center}

/* hero */
.hero{left:0;top:177px;width:1200px;height:740px;overflow:hidden}
.hero-bg{position:absolute;inset:0;background:radial-gradient(ellipse at 50% 40%,#3f5a73 0%,#223548 55%,#121c28 100%)}
.hero-title{left:0;top:252px;width:1200px;text-align:center;font-family:"Exo 2",sans-serif;font-weight:600;font-size:74px;color:var(--white)}
.hero-sub{left:0;top:350px;width:1200px;text-align:center;font-family:"Exo 2",sans-serif;font-size:21px;color:var(--white)}
.hero-btn{left:509px;top:418px;width:182px;height:56px;border:2px solid var(--white);border-radius:28px;background:var(--red);color:var(--white);font-family:"Exo 2",sans-serif;font-size:20px;display:flex;align-items:center;justify-content:center}
.hero-arrow{width:34px;height:34px;border:2px solid var(--white);border-radius:50%;display:flex;align-items:center;justify-content:center}

/* about */
.section-title{font-family:"Exo 2",sans-serif;font-weight:500;color:var(--ink)}
.section-title em{font-style:normal;color:var(--red)}
.about-title{left:110px;top:980px;font-size:50px}
.about-copy{left:110px;top:1075px;width:440px;font-size:12.5px;line-height:31px}
.about-copy p+p{margin-top:31px}
.outline-btn{border:2px solid var(--red);border-radius:31px;color:var(--red);font-family:"Exo 2",sans-serif;font-size:20px;display:flex;align-items:center;justify-content:center}
.about-btn{left:112px;top:1363px;width:170px;height:62px}
.hex-cluster{left:628px;top:995px;width:462px;height:458px}

/* services */
.services{left:0;top:1470px;width:1200px;height:740px}
.services-title{left:0;top:1600px;width:1200px;text-align:center;font-family:"Exo 2",sans-serif;font-weight:500;font-size:48px;color:var(--white)}
.services-lead{left:0;top:1677px;width:1200px;text-align:center;font-family:"Exo 2",sans-serif;font-size:13.5px;color:var(--white)}
.service{width:230px;text-align:center}
.service svg{display:block;margin:0 auto}
.service h3{font-family:"Exo 2",sans-serif;font-weight:500;font-size:15px;color:var(--white);margin-top:22px}
.service p{font-size:12px;line-height:26px;color:var(--muted);margin-top:14px}

/* strategy */
.strategy-kicker{left:0;top:2195px;width:1200px;text-align:center;font-family:"Exo 2",sans-serif;font-weight:500;font-size:32px;color:var(--ink)}
.strategy-title{left:0;top:2240px;width:1200px;text-align:center;font-family:"Exo 2",sans-serif;font-weight:600;font-size:40px;color:var(--red)}
.strategy-copy{left:220px;top:2315px;width:760px;text-align:center;font-size:12.5px;line-height:31px}
.strategy-photo{left:147px;top:2451px;width:533px;height:425px;background:linear-gradient(135deg,#9aa3a8,#5e676d 55%,#3c4348)}
.news-card{left:573px;top:2592px;width:472px;height:381px;background:var(--white);border:1px solid #e2e2e2;box-shadow:0 2px 10px rgba(0,0,0,.08);padding:26px 40px}
.news-card h2{font-family:"Exo 2",sans-serif;font-weight:500;font-size:48px;color:var(--ink)}
.news-card h2 em{font-style:normal;color:var(--red)}
.news-card p{font-size:12.3px;line-height:31px;margin-top:12px}
.news-btn{margin-top:18px;width:139px;height:50px;border-radius:25px;background:var(--red);color:var(--white);font-family:"Exo 2",sans-serif;font-size:15px;display:flex;align-items:center;justify-content:center}

/* leaders */
.leaders{left:0;top:3045px;width:1200px;height:425px;background:var(--pink-bg)}
.leaders-title{left:0;top:3075px;width:1200px;text-align:center;font-size:40px}
.leader-photo{width:166px;height:166px;border-radius:50%;background:radial-gradient(circle at 50% 40%,#8a8a8a,#2c2c2c)}
.leader-name{font-family:"Exo 2",sans-serif;font-weight:600;font-size:15px;color:var(--red);white-space:nowrap}
.leader-bio{width:264px;font-size:12px;line-height:26px;text-align:justify}

/* footer */
.footer{left:0;top:3440px;width:1200px;height:457px}
.footer-brand{left:0;top:3585px;width:1200px;display:flex;justify-content:center;align-items:center;gap:12px}
.footer-brand .brand-name{color:var(--white);font-size:38px}
.footer-brand .brand-mark{background:var(--white);width:28px;height:28px}
.footer-contact{left:0;top:3665px;width:1200px;display:flex;justify-content:center;gap:30px;font-family:"Open Sans",sans-serif;font-size:13px;color:var(--white)}
.footer-contact span{display:flex;align-items:center;gap:7px}
.footer-nav{left:0;top:3716px;width:1200px;display:flex;justify-content:center;font-family:"Open Sans",sans-serif;font-size:13px;color:var(--white)}
.footer-nav span{padding:0 20px;position:relative}
.footer-nav span+span::before{content:"/";position:absolute;left:-4px}
.social{left:0;top:3772px;width:1200px;display:flex;justify-content:center;gap:8px}
.social span{width:36px;height:36px;border:2px solid var(--white);border-radius:50%}
.copyright{left:0;top:3838px;width:1200px;text-align:center;font-family:"Open Sans",sans-serif;font-size:13px;color:var(--white)}
</style>
</head>
<body>

<header class="site-header abs">
  <div class="brand abs"><span class="brand-name">BORK VENTURES</span><span class="brand-mark"></span></div>
  <div class="tagline abs">Mission Integrity Results</div>
  <div class="call abs">
    <span class="call-icon"><svg width="18" height="18" viewBox="0 0 24 24"><path fill="#fff" d="M6.6 10.8a15 15 0 0 0 6.6 6.6l2.2-2.2c.3-.3.7-.4 1-.2 1.1.4 2.3.6 3.6.6.6 0 1 .4 1 1V20c0 .6-.4 1-1 1A17 17 0 0 1 3 4c0-.6.4-1 1-1h3.5c.6 0 1 .4 1 1 0 1.3.2 2.5.6 3.6.1.3 0 .7-.2 1z"/></svg></span>
    <span class="call-text">CALL US : 410-555-0172</span>
  </div>
</header>

<nav class="main-nav abs">
  <ul>
    <li class="active">HOME</li><li>ABOUT US</li><li>SERVICES</li><li>STRATEGY</li><li>IT NEWS</li><li>CONTACT US</li>
  </ul>
</nav>

<section class="hero abs">
  <div class="hero-bg" role="img" aria-label="Business professional holding floating network devices over a digital circuit background"></div>
  <h1 class="hero-title abs">BORK VENTURES</h1>
  <p class="hero-sub abs">BRINGING THOUGHT LEADERSHIP AND QUALITY TO EVERY PROJECT</p>
  <div class="hero-btn abs">GET STARTED</div>
  <div class="hero-arrow abs" style="left:68px;top:333px"><svg width="12" height="12" viewBox="0 0 12 12"><path d="M8 1 3 6l5 5" stroke="#fff" stroke-width="2" fill="none"/></svg></div>
  <div class="hero-arrow abs" style="left:1097px;top:333px"><svg width="12" height="12" viewBox="0 0 12 12"><path d="m4 1 5 5-5 5" stroke="#fff" stroke-width="2" fill="none"/></svg></div>
</section>

<svg class="abs" style="left:0;top:780px" width="1200" height="170" viewBox="0 0 1200 170">
  <path d="M0 15 Q600 130 1200 15 L1200 170 L0 170Z" fill="#fff"/>
  <path d="M0 18 Q300 95 560 120 L640 120 Q900 95 1200 18 Q900 110 640 120 L560 120 Q300 110 0 18Z" fill="var(--red)"/>
  <path d="M0 30 Q300 100 560 122" stroke="var(--red)" stroke-width="10" fill="none"/>
  <path d="M1200 30 Q900 100 640 122" stroke="var(--red)" stroke-width="10" fill="none"/>
  <circle cx="600" cy="100" r="50" fill="#fff" stroke="var(--red)" stroke-width="3"/>
  <rect x="585" y="85" width="30" height="30" fill="var(--red)"/>
</svg>

<h2 class="section-title about-title abs">ABOUT <em>US</em></h2>
<div class="about-copy abs">
  <p>Bork Ventures, Inc. is an 8(a) innovative and rapidly growing full-service IT consulting firm. We provide our clients with cutting-edge technologies and the know-how to apply them to their individual business models.</p>
  <p>For over 20 + years, we have been providing reliable IT solutions businesses in the Washington, DC Metro area and beyond. Our comprehensive services provide clients with unique technology solutions that are customized to meet the specific demands of their business.</p>
</div>
<div class="outline-btn about-btn abs">READ MORE</div>

<svg class="hex-cluster abs" viewBox="0 0 462 458">
  <g role="img" aria-label="Team of smiling business colleagues">
    <polygon points="115,4 228,70 228,200 115,266 2,200 2,70" fill="#c8d3dc" stroke="var(--red)" stroke-width="4"/>
  </g>
  <g role="img" aria-label="Professional woman touching a digital interface">
    <polygon points="345,4 458,70 458,200 345,266 232,200 232,70" fill="#b7c9d8" stroke="var(--red)" stroke-width="4"/>
  </g>
  <g role="img" aria-label="Rack of network server hardware">
    <polygon points="230,190 343,256 343,388 230,454 117,388 117,256" fill="#3a3d42" stroke="var(--red)" stroke-width="4"/>
  </g>
  <polygon points="230,66 330,124 330,240 230,298 130,240 130,124" fill="#fff"/>
  <text x="230" y="190" text-anchor="middle" font-family="'Exo 2',sans-serif" font-weight="700" font-size="20" fill="#222">BORK VENTURES</text>
</svg>

<svg class="services abs" viewBox="0 0 1200 740" preserveAspectRatio="none">
  <defs><linearGradient id="svc" x1="0" y1="0" x2="0" y2="1"><stop offset="0" stop-color="#a3173a"/><stop offset=".6" stop-color="#8b0c25"/><stop offset="1" stop-color="#6e0a1d"/></linearGradient></defs>
  <path d="M0 5 Q600 100 1200 0 L1200 730 Q600 620 0 730Z" fill="url(#svc)"/>
  <path d="M0 5 Q600 110 1200 0" stroke="#111" stroke-width="3" fill="none" transform="translate(0,2)"/>
  <path d="M0 728 Q600 612 1200 728" stroke="#111" stroke-width="3" fill="none"/>
  <path d="M0 730 Q600 620 1200 730 L1200 740 L0 740Z" fill="#fff"/>
</svg>
<h2 class="services-title abs">OUR SERVICES</h2>
<p class="services-lead abs">Bork Ventures, Inc. organizes our Services into four key areas. While these four services can be implemented individually</p>

<div class="service abs" style="left:120px;top:1760px">
  <svg width="140" height="156" viewBox="0 0 140 156"><polygon points="70,2 138,40 138,116 70,154 2,116 2,40" fill="none" stroke="#fff" stroke-width="1.5"/><rect x="50" y="58" width="40" height="40" fill="none" stroke="#fff" stroke-width="2"/><rect x="60" y="68" width="20" height="20" fill="none" stroke="#fff" stroke-width="2"/><path d="M56 50v8M64 50v8M72 50v8M80 50v8M56 98v8M64 98v8M72 98v8M80 98v8M42 64h8M42 72h8M42 80h8M42 88h8M90 64h8M90 72h8M90 80h8M90 88h8" stroke="#fff" stroke-width="2"/></svg>
  <h3>HARDWARE / SOFTWARE</h3>
  <p>We have access to multiple distributor partners throughout North America, as well as Elite Partner</p>
</div>
<div class="service abs" style="left:365px;top:1760px">
  <svg width="140" height="156" viewBox="0 0 140 156"><polygon points="70,2 138,40 138,116 70,154 2,116 2,40" fill="none" stroke="#fff" stroke-width="1.5"/><path d="M34 74a36 32 0 0 1 72 0Z" fill="none" stroke="#fff" stroke-width="2"/><path d="M34 74 62 104M106 74 78 104M70 42v32" stroke="#fff" stroke-width="2"/><circle cx="70" cy="112" r="11" fill="none" stroke="#fff" stroke-width="2"/><text x="70" y="117" text-anchor="middle" font-size="14" fill="#fff" font-family="Arial">$</text></svg>
  <h3>PROFESSIONAL SERVICES</h3>
  <p>Our team provides experienced leadership and guidance, utilizing the standard methodologies.</p>
</div>
<div class="service abs" style="left:610px;top:1760px">
  <svg width="140" height="156" viewBox="0 0 140 156"><polygon points="70,2 138,40 138,116 70,154 2,116 2,40" fill="none" stroke="#fff" stroke-width="1.5"/><circle cx="62" cy="62" r="20" fill="none" stroke="#fff" stroke-width="2"/><circle cx="62" cy="62" r="11" fill="none" stroke="#fff" stroke-width="2"/><path d="M62 62v34l10-6 8 20 14-6-8-18 12-2Z" fill="none" stroke="#fff" stroke-width="2" stroke-linejoin="round"/></svg>
  <h3>TECHNOLOGY ASSESSMENT</h3>
  <p>Experience has shown companies that perform objective, third-party technology assessments</p>
</div>
<div class="service abs" style="left:855px;top:1760px">
  <svg width="140" height="156" viewBox="0 0 140 156"><polygon points="70,2 138,40 138,116 70,154 2,116 2,40" fill="none" stroke="#fff" stroke-width="1.5"/><circle cx="56" cy="62" r="18" fill="none" stroke="#fff" stroke-width="2"/><circle cx="56" cy="56" r="6" fill="none" stroke="#fff" stroke-width="2"/><path d="M45 74a11 9 0 0 1 22 0" fill="none" stroke="#fff" stroke-width="2"/><circle cx="86" cy="94" r="18" fill="none" stroke="#fff" stroke-width="2"/><circle cx="86" cy="88" r="6" fill="none" stroke="#fff" stroke-width="2"/><path d="M75 106a11 9 0 0 1 22 0" fill="none" stroke="#fff" stroke-width="2"/></svg>
  <h3>TECHNOLOGY CONSULTING</h3>
  <p>Implementing quality solutions is more than applying technology to experts with deep technical</p>
</div>

<h2 class="strategy-kicker abs">OUR STRATEGY</h2>
<h2 class="strategy-title abs">YOUR PATH TO SUCCESS</h2>
<p class="strategy-copy abs">Civilian and Federal agencies are facing increased demands driven by the changing economic environment and shifts in the way products and services are sold and delivered. These factors have created an imperative to leverage new and innovative technology reduce cost and deliver profit-driving IT capabilities faster than ever before.</p>

<div class="strategy-photo abs" role="img" aria-label="Two engineers working at a terminal inside a server room"></div>
<article class="news-card abs">
  <h2>IT <em>NEWS</em></h2>
  <p>Sed ut perspiciatis unde omnis iste natus error sit voluptatem accus antium doloremque laudantium, totam rem aperiam, eaque ipsa quae ab illo inventore veritatis et quasi architecto beatae vitae dicta sunt explicabo. Nemo enim ipsam voluptatem quia voluptas sit aspernatur aut odit aut fugit, sed quia consequuntur magni dolores eos qui rati quia consequuntur one voluptatem sequi nesciunt.</p>
  <div class="news-btn">READ MORE</div>
</article>

<section class="leaders abs"></section>
<h2 class="section-title leaders-title abs">OUR <em>LEADERS</em></h2>
<div class="leader-photo abs" style="left:110px;top:3185px" role="img" aria-label="Portrait photo of the co-founder"></div>
<div class="leader-name abs" style="left:306px;top:3188px">ARVIN DESHPAL- CO-FOUNDER</div>
<p class="leader-bio abs" style="left:304px;top:3222px">Arvin has played a leading role in the global information technology industry for more than 20 years, managing divisions and business the United States. Since founding Bork Ventures, Inc. (BVI) in 2008, he has been instrumental in formulating the company's strategy and organization's core competencies.</p>
<div class="leader-photo abs" style="left:629px;top:3185px" role="img" aria-label="Portrait photo of the chief technology officer"></div>
<div class="leader-name abs" style="left:823px;top:3188px">DORIAN WELLES - CHIEF TECHNOLOGY</div>
<p class="leader-bio abs" style="left:823px;top:3222px">Dorian Welles is the Chief Technology Officer for Bork Ventures, INC. Mr. Welles, an eighteen-year veteran in the IT industry, is responsible for developing the overall technology vision for the company, driving cross-company engineering initiatives and collaboration, and overseeing BVI's vendor partnerships.</p>

<svg class="footer abs" viewBox="0 0 1200 457" preserveAspectRatio="none">
  <path d="M0 20 Q600 70 1200 20 L1200 457 L0 457Z" fill="var(--footer)"/>
  <path d="M0 14 Q600 66 1200 14" stroke="var(--red)" stroke-width="8" fill="none"/>
</svg>
<div class="footer-brand abs"><span class="brand-name">BORK VENTURES</span><span class="brand-mark"></span></div>
<div class="footer-contact abs">
  <span><svg width="10" height="14" viewBox="0 0 10 14"><path d="M5 0a5 5 0 0 1 5 5c0 4-5 9-5 9S0 9 0 5a5 5 0 0 1 5-5Z" fill="#c8304f"/><circle cx="5" cy="5" r="2" fill="var(--footer)"/></svg>2280 Harrowgate Ln Calder Springs, MD 20901</span>
  <span><svg width="12" height="12" viewBox="0 0 24 24"><path fill="#c8304f" d="M6.6 10.8a15 15 0 0 0 6.6 6.6l2.2-2.2c.3-.3.7-.4 1-.2 1.1.4 2.3.6 3.6.6.6 0 1 .4 1 1V20c0 .6-.4 1-1 1A17 17 0 0 1 3 4c0-.6.4-1 1-1h3.5c.6 0 1 .4 1 1 0 1.3.2 2.5.6 3.6.1.3 0 .7-.2 1z"/></svg>410-555-0172</span>
  <span><svg width="13" height="10" viewBox="0 0 13 10"><rect width="13" height="10" fill="#c8304f"/><path d="m0 0 6.5 5L13 0" stroke="var(--footer)" fill="none"/></svg>hello@borkventures.example</span>
</div>
<div class="footer-nav abs"><span>HOME</span><span>ABOUT US</span><span>SERVICES</span><span>STRATEGY</span><span>IT NEWS</span><span>CONTACT US</span></div>
<div class="social abs"><span></span><span></span><span></span><span></span><span></span></div>
<p class="copyright abs">© Copyright-2019 Bork Ventures.All rights reserved.</p>

</body>
</html>
```